Social Media App Needs PPT Template

We need a PowerPoint template for a new social media company based in the DC area called "Bold Ledger." We provide an interactive digital platform for executives to share actionable advice. We would like to see designs that use our orange logo color as an accent, but are mainly grey, white, and black. The final design should communicate clean, chic, modern, and professional.

Target Market(s)

Executives

Industry/Entity Type

Information Technology

Font styles to use
Sans Serif

Colors
f78f20
fbe7d2
ffffff
000000
e8e8e8
757575

Requirements
Must have
• My project must have title page and many options for the body of the ppt (graphs, tables, etc). It also needs to be easy to modify. I must have someone who is experienced in creating powerpoint templates.
Nice to have
• It would be nice to have a very modern and clean design that includes the logo on every page, but still leaves a lot of room for the content of the slide
Should not have
• My design project should not look to busy.

```html
<!DOCTYPE html>
<html lang="en">
<head>
<meta charset="utf-8">
<title>About Our Company – Bold Ledger</title>
<link rel="stylesheet" href="https://fonts.googleapis.com/css2?family=Lato:wght@300;400;700&display=swap">
<style>
  :root {
    --backdrop: #929292;
    --orange: #e8861c;
    --orange-light: #f39a2a;
    --charcoal: #474747;
    --ink: #2b2b2b;
    --paper: #f7f7f7;
    --paper-edge: #ececec;
    --white: #ffffff;
  }
  * { margin: 0; padding: 0; box-sizing: border-box; }
  html, body {
    width: 1200px; height: 960px; overflow: hidden;
    background: var(--backdrop);
    font-family: "Lato", sans-serif;
  }
  .slide {
    position: absolute; left: 87px; top: 128px;
    width: 1046px; height: 784px; overflow: hidden;
    background: radial-gradient(ellipse at 50% 40%, var(--white) 0%, var(--paper) 45%, var(--paper-edge) 100%);
  }
  .header-art { position: absolute; left: 0; top: 0; width: 1046px; height: 150px; }
  .slide-title {
    position: absolute; left: 32px; top: 70px;
    font-weight: 300; font-size: 39px; color: var(--white); letter-spacing: 0.2px;
  }
  .brand {
    position: absolute; left: 846px; top: 72px;
    display: flex; align-items: center; gap: 10px;
  }
  .brand-dot { width: 22px; height: 22px; border-radius: 50%; background: var(--orange); }
  .brand-name { font-weight: 700; font-size: 22px; color: var(--white); letter-spacing: 0.5px; }
  .feature { position: absolute; top: 230px; width: 274px; }
  .feature-icon { display: block; height: 120px; margin: 0 auto; }
  .feature-text {
    margin-top: 65px;
    font-size: 18.5px; line-height: 26.7px; color: var(--ink);
    text-align: justify; text-align-last: center; hyphens: manual;
  }
  .feature--growth { left: 48px; }
  .feature--partner { left: 387px; }
  .feature--approval { left: 721px; }
  .footer-art { position: absolute; left: 0; top: 742px; width: 1046px; height: 31px; }
  .footer-text {
    position: absolute; left: 28px; top: 749px;
    font-size: 14px; color: #e6e6e6;
  }
  .footer-text .sep { margin: 0 7px; }
</style>
</head>
<body>
<main class="slide">
  <svg class="header-art" viewBox="0 0 1046 150" aria-hidden="true">
    <defs>
      <linearGradient id="bandGrad" x1="0" y1="0" x2="1" y2="0">
        <stop offset="0" stop-color="#e57f16"/>
        <stop offset="0.7" stop-color="#ea8a1e"/>
        <stop offset="1" stop-color="#f29b2c"/>
      </linearGradient>
    </defs>
    <polygon points="813,34 1046,34 1046,44 803,44" fill="var(--orange)"/>
    <polygon points="0,49 793,49 712,130 0,130" fill="url(#bandGrad)"/>
    <polygon points="560,49 793,49 740,102 510,102" fill="#f4a03a" opacity="0.25"/>
    <polygon points="0,112 730,112 712,130 0,130" fill="#e37c12" opacity="0.5"/>
    <polygon points="800,49 1046,49 1046,130 719,130" fill="var(--charcoal)"/>
    <polygon points="0,135 706,135 696,145 0,145" fill="var(--charcoal)"/>
  </svg>
  <h1 class="slide-title">About Our Company</h1>
  <div class="brand">
    <span class="brand-dot"></span>
    <span class="brand-name">Bold Ledger</span>
  </div>

  <section class="feature feature--growth">
    <svg class="feature-icon" viewBox="0 0 150 110" width="150" aria-hidden="true">
      <g fill="none" stroke="var(--charcoal)" stroke-width="6" stroke-linejoin="round" stroke-linecap="round">
        <rect x="9" y="4" width="132" height="92" rx="2"/>
        <rect x="21" y="16" width="108" height="68"/>
        <path d="M38 62 L58 48 L78 60 L108 32"/>
        <rect x="3" y="96" width="144" height="10" rx="2"/>
      </g>
    </svg>
    <p class="feature-text">Duis autem vel eum iriure dolor in hendrerit in vulputate velit esse molestie consequat, vel illum dolore eu feugiat nulla facilisis at vero eros et accumsan et iusto odio dignissim qui blan&shy;dit praesent luptatum zzril del enit augue duis dolore te feugait nulla facilisi.</p>
  </section>

  <section class="feature feature--partner">
    <svg class="feature-icon" viewBox="0 0 140 110" width="140" aria-hidden="true">
      <g fill="none" stroke="var(--orange)" stroke-width="6" stroke-linejoin="round" stroke-linecap="round">
        <rect x="4" y="14" width="26" height="20" transform="rotate(-40 17 24)"/>
        <rect x="110" y="14" width="26" height="20" transform="rotate(40 123 24)"/>
        <path d="M26 40 L38 60 L50 72 L66 90 Q74 98 82 90 L110 62 L118 44"/>
        <path d="M44 44 L68 38 L90 48 L76 56 Q66 60 58 52"/>
        <path d="M112 36 L96 42 L90 48"/>
        <circle cx="42" cy="76" r="5"/>
        <circle cx="52" cy="86" r="5"/>
        <circle cx="62" cy="94" r="5"/>
        <path d="M88 72 L98 82 M80 80 L90 90 M96 64 L106 74"/>
      </g>
    </svg>
    <p class="feature-text">Duis autem vel eum iriure dolor in hendrerit in vulputate velit esse molestie consequat, vel illum dolore eu feugiat nulla facilisis at vero eros et accumsan et iusto odio dignissim qui blan&shy;dit praesent luptatum zzril dele nit augue duis dolore te feugait nulla facilisi.</p>
  </section>

  <section class="feature feature--approval">
    <svg class="feature-icon" viewBox="0 0 110 110" width="110" aria-hidden="true">
      <g fill="none" stroke="var(--charcoal)" stroke-width="6" stroke-linejoin="round" stroke-linecap="round">
        <rect x="4" y="48" width="16" height="46"/>
        <rect x="20" y="44" width="18" height="54"/>
        <path d="M38 50 L56 34 Q64 24 66 10 Q68 2 76 6 Q84 12 80 30 L76 42 L100 42 Q108 44 106 54 Q104 60 98 60 Q106 64 102 72 Q100 76 96 76 Q102 82 96 88 Q94 92 88 92 L88 96 Q86 102 80 102 L54 102 Q44 100 38 94"/>
      </g>
      <circle cx="29" cy="58" r="3" fill="var(--charcoal)"/>
    </svg>
    <p class="feature-text">Duis autem vel eum iriure dolor in hendrerit in vulputate velit esse molestie consequat, vel illum dolore eu feugiat nulla facilisis at vero eros et accumsan et iusto odio dignissim qui blan&shy;dit praesent luptatum zzril del enit augue duis dolore te feugait nulla facilisi.</p>
  </section>

  <svg class="footer-art" viewBox="0 0 1046 31" aria-hidden="true">
    <polygon points="0,0 299,0 266,31 0,31" fill="var(--charcoal)"/>
    <polygon points="305,0 1046,0 1046,31 273,31" fill="var(--orange)"/>
  </svg>
  <p class="footer-text">www.boldledger.com<span class="sep">|</span>Page 3</p>
</main>
</body>
</html>
```